Business Card design for law firm = Brightvale Australia

We are seeking a new design for our business cards.
We are keeping our logo, which is attached.
We need space for
Name
Title
Address is , which is
Level 7
214 Marlowe Street
Sydney NSW 2047
Phone :
Mobile :
Fax :
Email :
DX :
website www.brightvale-example.com.au

Industry/Entity Type

Law Firm / Banking and Finance

Contact Information for Business Card

We are seeking a new design for our business cards. We are keeping our logo. We need space for Name Title Address is Level 7 214 Marlowe Street Sydney NSW 2047 Phone Mobile Fax Email DX website www.brightvale-example.com.au

Colors
0054AA
0677BA
7BADD7
CADEEF
E8F1F8

Requirements
Must have
• see our website for general feel www.brightvale-example.com.au

```html
<!DOCTYPE html>
<html lang="en">
<head>
<meta charset="utf-8">
<title>Brightvale Australia – Business Card</title>
<link rel="stylesheet" href="https://fonts.googleapis.com/css2?family=Questrial&family=Montserrat:wght@700&display=swap">
<style>
  :root {
    --bg: #1e2124;
    --card: #ffffff;
    --navy: #0054aa;
    --blue: #0677ba;
    --band: #1f5fad;
    --ink: #1b1b1b;
    --light: #ffffff;
  }
  * { margin: 0; padding: 0; box-sizing: border-box; }
  html, body { width: 1200px; height: 1000px; overflow: hidden; background: var(--bg); }
  body { position: relative; font-family: "Questrial", "Helvetica Neue", Arial, sans-serif; }

  .card {
    position: absolute;
    width: 540px; height: 330px;
    background: var(--card);
    overflow: hidden;
    box-shadow: 0 14px 30px rgba(0,0,0,.45);
  }
  .card--front { left: 70px; top: 90px; }
  .card--back  { left: 590px; top: 520px; }

  .brand { position: absolute; color: var(--navy); line-height: 1; white-space: nowrap; }
  .card--front .brand { left: 150px; top: 140px; font-size: 48px; }
  .card--back .brand { right: 34px; top: 30px; font-size: 24px; }

  .band {
    position: absolute; left: 120px; right: 0; top: 140px; height: 160px;
    background: var(--band);
  }

  .identity { position: absolute; left: 40px; top: 34px; color: var(--ink); }
  .identity__name {
    font-family: "Montserrat", Arial, sans-serif; font-weight: 700;
    font-size: 26px; color: var(--blue); letter-spacing: 1px; line-height: 1;
  }
  .identity__title { font-size: 10px; letter-spacing: .5px; margin-top: 4px; }
  .identity__rule { width: 150px; height: 1.5px; background: var(--blue); margin: 6px 0 7px; }
  .identity__address { font-size: 13px; line-height: 18px; }

  .contacts { position: absolute; left: 146px; top: 156px; list-style: none; color: var(--light); }
  .contacts li { display: flex; align-items: center; gap: 12px; font-size: 13px; height: 26px; }
  .contacts svg { width: 14px; height: 14px; flex: none; fill: var(--light); }
  .contacts .label-dx { width: 14px; font-size: 12px; }
</style>
</head>
<body>

  <section class="card card--front" aria-label="Business card front">
    <p class="brand">Brightvale</p>
  </section>

  <section class="card card--back" aria-label="Business card back">
    <p class="brand">Brightvale</p>

    <div class="band"></div>

    <div class="identity">
      <p class="identity__name">NAME</p>
      <p class="identity__title">MANAGING DIRECTOR</p>
      <div class="identity__rule"></div>
      <p class="identity__address">Level 7, 214 Marlowe Street<br>Sydney NSW 2047</p>
    </div>

    <ul class="contacts">
      <li>
        <svg viewBox="0 0 16 16" aria-hidden="true"><circle cx="8" cy="8" r="8"/><path d="M5 4.5l1.5-.5 1 2-1 .8c.4 1 1.2 1.8 2.2 2.2l.8-1 2 1-.5 1.5c-3 .3-6.3-3-6-6z" fill="#1f5fad"/></svg>
        <span>02 9000 0142</span>
      </li>
      <li>
        <svg viewBox="0 0 16 16" aria-hidden="true"><rect x="4" y="1" width="8" height="5"/><rect x="1" y="6" width="14" height="7" rx="1"/><rect x="4" y="10" width="8" height="5"/></svg>
        <span>02 9000 0187</span>
      </li>
      <li>
        <svg viewBox="0 0 16 16" aria-hidden="true"><rect x="1" y="3" width="14" height="10"/><path d="M1 3l7 6 7-6" fill="none" stroke="#1f5fad" stroke-width="1.4"/></svg>
        <span>enquiries@brightvale-example.com.au</span>
      </li>
      <li>
        <span class="label-dx">DX</span>
        <span>318 Sydney</span>
      </li>
      <li>
        <svg viewBox="0 0 16 16" aria-hidden="true"><circle cx="8" cy="8" r="7" fill="none" stroke="#fff" stroke-width="1.3"/><ellipse cx="8" cy="8" rx="3" ry="7" fill="none" stroke="#fff" stroke-width="1.1"/><path d="M1 8h14M2.5 4.5h11M2.5 11.5h11" stroke="#fff" stroke-width="1"/></svg>
        <span>www.brightvale-example.com.au</span>
      </li>
    </ul>
  </section>

</body>
</html>
```